Restaurant Menu New Design

Hello Designers,

Blue Fern is a casual family oriented dine-in restaurant, we serve American Italian dishes like Pizza, Pasta, and Sandwiches.

We are excited about adding some new delicious dishes and recipes to our menu. And we are looking for a talented and creative designer to design it.

The menu is a 12 page black leather book, page size is:
6.5" X 11.69" (16.51 cm X 29.69 cm)

Below is the scope of work and requirements:

1) Design a completely all new, creative, and beautiful menu, including cover page, blue fern oven intro. page, interior pages, and kids menu page.

2) Design a take out edition of the menu. It will be exactly the same as the dine-in menu, but with the addition of a back cover page with info such as contacts, social media, location map, etc…

3) Files are required in Adobe Illustrator format. Layers should be organized, all text should be editable, and all the food pictures easy to change.

4) This is a two language menu, so you are required to make space in the design for a second language. The easiest way to do that is have every item listed in English twice, then I will edit the second text with Illustrator.

5) In your initial design submission, the minimum you are required to submit are these 4 pages:
– Cover page
– Typical interior menu page
– Kids menu page
– Take-out menu back cover page

If your initial design is selected, then you are required to submit all remaining pages to complete the project.

In the link below, you will find:
1) Logo
2) New menu text in Excel
3) Food images (will take some time to upload)
4) The old dine-in and take out menu designs

https://www.filevaultra.com/sh/kq7tmwzabe3pxd/BBBrTnpLk41QaWmZpQ8V2X7Jd?dl=0

Thank you for stopping by and reading this brief. I hope you like this project and enjoy designing our new menu. Please let me know if you have any questions.

Cheers!

Project Deadline Extended
Reason: We have decided to extend the deadline due to the low number of submissions which was much lower than the expected submissions we were give by Brief Harbor.

```html
<!DOCTYPE html>
<html lang="en">
<head>
<meta charset="utf-8">
<title>Blue Fern — Pizza Menu Page</title>
<link rel="stylesheet" href="https://fonts.googleapis.com/css2?family=Lato:wght@400;700&family=Noto+Naskh+Arabic:wght@400;600&display=swap">
<style>
  :root {
    --board: #353535;
    --chalk: #ffffff;
    --chalk-soft: #e6e6e6;
    --muted: #b3b3b3;
    --line: #d9d9d9;
    --photo-warm-a: #8a5a2e;
    --photo-warm-b: #c9923f;
    --photo-dark: #1f1f1f;
    --sketch: #5a5a5a;
  }
  * { margin: 0; padding: 0; box-sizing: border-box; }
  html, body {
    width: 1200px; height: 2177px; overflow: hidden;
    background: var(--board);
  }
  .menu-page {
    position: absolute; top: 0; left: 0;
    width: 827px; height: 1500px;
    transform: scale(1.451); transform-origin: 0 0;
    background: var(--board);
    font-family: "Lato", Arial, sans-serif;
    color: var(--chalk);
  }
  .chalk-lines { position: absolute; inset: 0; width: 827px; height: 1500px; }
  .section-title {
    position: absolute; top: 46px; width: 200px;
    text-align: center; font-size: 26px; font-weight: 400; letter-spacing: 0.5px;
  }
  .section-title--left { left: 122px; }
  .section-title--right { left: 505px; }

  .sketch {
    position: absolute; border-radius: 6px;
    background: var(--sketch); opacity: 0.55;
  }
  .photo { position: absolute; width: 297px; height: 198px; }
  .photo--spicy-beef { left: 73px; top: 180px;
    background: radial-gradient(circle at 50% 55%, var(--photo-warm-b) 0 38%, var(--photo-dark) 39% 47%, var(--photo-warm-a) 48%); }
  .photo--pepperoni { left: 460px; top: 180px;
    background: linear-gradient(120deg, #2a2a2a 0%, #b2442d 35%, #e9c98a 60%, #c2572f 85%, #2a2a2a 100%); }
  .photo--chicken-teriyaki { left: 73px; top: 570px;
    background: radial-gradient(circle at 50% 50%, #d79a4d 0 40%, #2b2b2b 41% 47%, #4a3426 48%); }

  .item { position: absolute; width: 300px; text-align: center; }
  .item h2 {
    font-size: 17px; font-weight: 700; line-height: 22px; color: var(--chalk);
  }
  .item h2 .ar-title, .item .ar {
    font-family: "Noto Naskh Arabic", "Lato", serif;
  }
  .item h2 .ar-title { font-weight: 600; }
  .item .desc {
    margin: 10px auto 0; max-width: 250px;
    font-size: 12px; line-height: 15px; color: var(--muted);
  }
  .item .desc--bright {
    font-family: Arial, "Lato", sans-serif; color: var(--chalk-soft); max-width: 260px;
  }
  .item .ar {
    margin: 10px auto 0; max-width: 250px;
    font-size: 11px; line-height: 15px; color: var(--muted); direction: rtl;
  }
</style>
</head>
<body>
<main class="menu-page">

  <svg class="chalk-lines" viewBox="0 0 827 1500" aria-hidden="true" fill="none" stroke="var(--line)" stroke-width="1.5">
    <!-- header rules -->
    <line x1="0" y1="87" x2="290" y2="87"/>
    <line x1="620" y1="87" x2="827" y2="87"/>
    <!-- top-left frame -->
    <polyline points="190,153 47,153 47,300"/>
    <polyline points="190,160 55,160 55,260"/>
    <polyline points="383,300 383,395 230,395"/>
    <polyline points="376,330 376,388 280,388"/>
    <!-- top-right frame -->
    <polyline points="460,153 560,153"/>
    <polyline points="460,160 520,160"/>
    <polyline points="780,220 780,395 700,395"/>
    <!-- section divider -->
    <line x1="0" y1="540" x2="330" y2="540"/>
    <line x1="520" y1="540" x2="827" y2="540"/>
    <!-- left wave -->
    <path d="M48 560 C30 600 60 640 42 680 C26 720 56 760 40 790"/>
    <!-- right frame lower -->
    <polyline points="780,555 780,840 640,840"/>
    <line x1="0" y1="1115" x2="105" y2="1115"/>
    <line x1="700" y1="1120" x2="827" y2="1120"/>
    <polyline points="710,1240 775,1240 775,1300"/>
    <!-- bottom divider -->
    <line x1="0" y1="1438" x2="335" y2="1438"/>
    <line x1="495" y1="1438" x2="827" y2="1438"/>
  </svg>

  <h1 class="section-title section-title--left">PIZZA</h1>
  <h1 class="section-title section-title--right">PIZZA</h1>

  <div class="sketch" style="left:370px;top:52px;width:90px;height:56px" role="img" aria-label="Line sketch of a serving cloche"></div>
  <div class="sketch" style="left:165px;top:102px;width:120px;height:36px" role="img" aria-label="Line sketches of tomato, onion and pepper"></div>
  <div class="sketch" style="left:528px;top:102px;width:165px;height:38px" role="img" aria-label="Line sketches of peas, lemon and mushrooms"></div>
  <div class="sketch" style="left:330px;top:527px;width:190px;height:22px" role="img" aria-label="Line sketch of a rolling pin"></div>
  <div class="sketch" style="left:335px;top:1425px;width:160px;height:22px" role="img" aria-label="Line sketch of a rolling pin"></div>
  <div class="sketch" style="left:390px;top:178px;width:40px;height:290px;opacity:.3" role="img" aria-label="Line sketches of a spatula, onion, tomato and chili"></div>
  <div class="sketch" style="left:395px;top:610px;width:50px;height:760px;opacity:.3" role="img" aria-label="Column of line sketches of eggplant, mushroom, carrot, pomegranate, pear and fruits"></div>

  <div class="photo photo--spicy-beef" role="img" aria-label="Photo of a spicy beef pizza in a pan"></div>
  <div class="photo photo--pepperoni" role="img" aria-label="Photo of a pepperoni pizza slice with stretching cheese"></div>
  <div class="photo photo--chicken-teriyaki" role="img" aria-label="Photo of a cashew chicken teriyaki pizza"></div>

  <article class="item" style="left:62px;top:398px">
    <h2>SPICEY BEEF | <span class="ar-title">اللحم الحارق</span></h2>
    <p class="desc">Spicy ground beef, pepperoni, white onions, bell peppers, and cilantro&nbsp; 37</p>
    <p class="ar">لحم مفروم مبهر بالفلفل الحارق، ببروني، بصل أبيض، فلفل رومي، كزبرة&nbsp; 37</p>
  </article>

  <article class="item" style="left:462px;top:398px">
    <h2>PEPPERONI | <span class="ar-title">بيبيروني</span></h2>
    <p class="desc">Pepperoni slices, mozzarella, cheese,tomato</p>
    <p class="ar">شرائح البيبيروني وجبنة الموزاريلا وصلصة الطماطم&nbsp; 34</p>
  </article>

  <article class="item" style="left:462px;top:569px">
    <h2>SHRIMP FAJITA |<br><span class="ar-title">فاهيتا الجمبري</span></h2>
    <p class="desc desc--bright">Fajita shrimps, tomato sauce, mozzarella &amp; cheddar cheese, onions, green &amp; red bell peppers, cilantro&nbsp; 42</p>
    <p class="ar">جمبري بصوص الفاهيتا، صلصة الطماطم، جبنة موزاريلا وتشيدر، شرائح البصل والفلفل الرومي الأخضر والأحمر، كزبرة&nbsp; 42</p>
  </article>

  <article class="item" style="left:462px;top:756px">
    <h2>CHEESE | <span class="ar-title">جبنة</span></h2>
    <p class="desc">Mozzarella cheese &amp; tomato sauce&nbsp; 27</p>
    <p class="ar">جبنة الموزاريلا وصلصة الطماطم&nbsp; 27</p>
  </article>

  <article class="item" style="left:462px;top:859px">
    <h2>GREEK | <span class="ar-title">بيتزا يونانية</span></h2>
    <p class="desc">Tomatos, kalamata olives,greenbell peppers, spinach,tomato sauce, mozzarella&amp;crumbledfeta</p>
    <p class="ar">قطع الطماطم، زيتون، فلفل رومي أخضر، سبانخ، صلصة الطماطم، جبنة فيتا وجبنة الموزاريلا&nbsp; 35</p>
  </article>

  <article class="item" style="left:462px;top:1025px">
    <h2>VEGGIE | <span class="ar-title">خضروات</span></h2>
    <p class="desc">Mushrooms, green peppers,onions, black olives&nbsp; 32</p>
    <p class="ar">فطر، فلفل رومي أخضر، بصل وزيتون&nbsp; 32</p>
  </article>

  <article class="item" style="left:462px;top:1130px">
    <h2>MUSHROOMS | <span class="ar-title">فطر</span></h2>
    <p class="desc">Mushrooms, tomato sauce, mozzarella&nbsp; 34</p>
    <p class="ar">فطر وصلصة الطماطم والموزاريلا&nbsp; 34</p>
  </article>

  <article class="item" style="left:462px;top:1259px">
    <h2>BEEF TERIYAKI PIZZAC51 |<br><span class="ar-title">بيتزا تيرياكي لحم</span></h2>
    <p class="desc">Thin slices of Teriyaki beef, sesame, red bell peppers,spring onions, mozzarella cheese&nbsp; 39</p>
    <p class="ar">شرائح اللحم الخفيفة بصوص التيرياكي والسمسم، فلفل رومي أحمر، بصل أخضر وجبنة الموزاريلا سائحة</p>
  </article>

  <article class="item" style="left:78px;top:797px">
    <h2>CAHSHEW CHICKEN TERIYAKI |<br><span class="ar-title">تيرياكي الدجاج والكاشو</span></h2>
    <p class="desc">Teriyaki chicken strips, sesame, crunchy cashews, red bell peppers, spring onions, mozzarella cheese&nbsp; 37</p>
    <p class="ar">دجاج بصوص التيرياكي والسمسم، كاشو مقرمش، فلفل رومي أحمر، بصل أخضر وجبنة الموزاريلا سائحة&nbsp; 37</p>
  </article>

  <article class="item" style="left:78px;top:992px">
    <h2>HAWAIIAN | <span class="ar-title">هاواي</span></h2>
    <p class="desc">Pineapples, bacon, red onions, tomato sauce, mozzarella cheese&nbsp; 37</p>
    <p class="ar">قطع الأناناس، بيكون، بصل أحمر، صلصة الطماطم، الموزاريلا&nbsp; 37</p>
  </article>

  <article class="item" style="left:78px;top:1131px">
    <h2>HAWAIIAN BBQ CHICKEN |<br><span class="ar-title">هاواي باربيكيو الدجاج</span></h2>
    <p class="desc">BBQ chicken, pineapple, bacon, mozzarella, red onions, cilantro&nbsp; 37</p>
    <p class="ar">دجاج بصوص الباربيكيو، أناناس، بيكون، موزاريلا، بصل أحمر وكزبرة خضراء&nbsp; 37</p>
  </article>

  <article class="item" style="left:78px;top:1294px">
    <h2>BBQ CHICKEN | <span class="ar-title">باربيكيو الدجاج</span></h2>
    <p class="desc" style="max-width:110px">BBQ chicken, mozzarella, cilantro, red onions&nbsp; 37</p>
    <p class="ar" style="margin-top:0">بصوص الباربيكيو، موزاريلا، بصل أحمر وكزبرة خضراء&nbsp; 37</p>
  </article>

</main>
</body>
</html>
```